New Web Site Design - Tallow Ridge Communication Solutions

We are looking for a completely new web site design. Tallow Ridge Communication Solutions is a full service company providing PBX and IP/Cloud Based phone systems. We also sell and install video camera surveillance systems and provide low voltage cabling services (CAT5 and CAT3). We are looking for something professional looking. We want to be able to showcase our vendor partners as well as be able to show photos of some of the work we have done. We will also want to be able to post PDF brochures as well as make changes to the website ourselves.

Target Market(s)

Commercial

Industry/Entity Type

Communication

Coding

Coded - Design and coding required

Number of Pages Required

5+ page

Font styles to use
Sans Serif

Colors
0455a3

Requirements
Must have
• Ability to upload PDF brochures
• Professional look and feel
• Ability to upload and easily insert job photos
• Thinking it should have at least 6 pages: Main page, phone systems and services page, carrier services page, video surveillance systems and service page, low voltage cabling services page, contact us page

```html
<!DOCTYPE html>
<html lang="en">
<head>
<meta charset="utf-8">
<title>Tallow Ridge Communication Solutions</title>
<link rel="stylesheet" href="https://fonts.googleapis.com/css2?family=Mulish:wght@400;500&family=Roboto:wght@400&display=swap">
<style>
  :root{
    --navy:#0b2a5b;
    --text-grey:#6f6f6f;
    --nav-grey:#7d7d7d;
    --hero-slate:#4f5567;
    --band-grey:#f2f2f2;
    --footer-dark:#2b2b2b;
    --footer-text:#b9b9b9;
    --white:#ffffff;
  }
  *{margin:0;padding:0;box-sizing:border-box}
  html,body{width:1200px;height:1089px;overflow:hidden;background:var(--white)}
  body{position:relative;font-family:"Roboto",sans-serif;color:var(--text-grey)}

  .site-header{position:absolute;left:0;top:0;width:1200px;height:101px;background:var(--white)}
  .brand{position:absolute;left:99px;top:27px}
  .brand-name{font-family:"Mulish",sans-serif;font-weight:500;font-size:19px;line-height:22px;color:var(--navy)}
  .main-nav{position:absolute;right:100px;top:37px;display:flex;gap:32px;font-family:"Mulish",sans-serif;font-size:13px}
  .main-nav a{color:var(--nav-grey);text-decoration:none}
  .main-nav a.is-active{color:var(--navy)}

  .hero{position:absolute;left:0;top:101px;width:1200px;height:429px}
  .hero-photo{position:absolute;inset:0;background:linear-gradient(90deg,#d8d3cf 0%,#c9b4a6 20%,#8a8580 40%,#5b5d63 60%,var(--hero-slate) 75%,var(--hero-slate) 100%)}
  .hero-copy{position:absolute;right:99px;top:132px;width:360px;text-align:right;color:var(--white)}
  .hero-title{font-family:"Mulish",sans-serif;font-weight:400;font-size:24px;line-height:31px}
  .hero-text{margin-top:14px;font-size:11px;line-height:20.5px;color:#e2e3e8}
  .slider-dots{position:absolute;left:1016px;top:285px;width:84px;height:19px;border-radius:10px;background:#393e4d;display:flex;align-items:center;justify-content:center;gap:9px}
  .slider-dots span{width:8px;height:8px;border-radius:50%;background:#e6e6e6}
  .slider-dots span.is-current{background:transparent;border:1.5px solid #e6e6e6}

  .services{position:absolute;left:0;top:530px;width:1200px;height:312px}
  .service{position:absolute;top:52px;width:205px}
  .service-icon{width:84px;height:84px;border-radius:50%;border:1px solid var(--navy);display:flex;align-items:center;justify-content:center}
  .service-icon.is-filled{background:var(--navy)}
  .service-title{margin-top:12px;height:45px;font-family:"Mulish",sans-serif;font-weight:400;font-size:19px;line-height:22.5px;color:var(--navy)}
  .service-title.is-single{padding-top:11px}
  .service-text{margin-top:10px;font-size:10px;line-height:17px;color:var(--text-grey)}

  .cta-band{position:absolute;left:0;top:842px;width:1200px;height:145px;background:var(--band-grey);text-align:center}
  .cta-line{margin-top:39px;font-family:"Mulish",sans-serif;font-size:17px;color:#4a4a4a}
  .cta-button{display:inline-block;margin-top:12px;width:108px;height:40px;line-height:38px;border:1px solid #a8a8a8;font-family:"Mulish",sans-serif;font-size:13px;color:#4a4a4a;text-decoration:none}

  .site-footer{position:absolute;left:0;top:987px;width:1200px;height:102px;background:var(--footer-dark)}
  .footer-nav{position:absolute;left:99px;top:29px;font-size:11px;color:var(--footer-text)}
  .footer-nav a{color:var(--footer-text);text-decoration:none}
  .footer-nav .sep{margin:0 8px}
  .copyright{position:absolute;left:99px;top:57px;font-size:11px;color:var(--footer-text)}
  .social{position:absolute;left:998px;top:37px;display:flex;gap:11px}
  .social span{width:26px;height:26px;border-radius:50%}
</style>
</head>
<body>
  <header class="site-header">
    <div class="brand">
      <div class="brand-name">Tallow Ridge<br>Communication Solutions</div>
    </div>
    <nav class="main-nav">
      <a class="is-active" href="#">Home</a>
      <a href="#">Phone systems</a>
      <a href="#">Video Surveillance</a>
      <a href="#">Low voltage cabling</a>
      <a href="#">Carrier</a>
      <a href="#">Contact us</a>
    </nav>
  </header>

  <section class="hero">
    <div class="hero-photo" role="img" aria-label="Technician plugging a red network cable into a phone system rack"></div>
    <div class="hero-copy">
      <h1 class="hero-title">Welcome to<br>Tallow Ridge Communications</h1>
      <p class="hero-text">Nulla tristique posuere molestie. Aliquam erat volutpat. Etiam quis aliquet risus. Duis ornare erat eget magna dapibus, in accumsan quam pharetra quam in bibendum vulputate.</p>
    </div>
    <div class="slider-dots"><span class="is-current"></span><span></span><span></span><span></span></div>
  </section>

  <section class="services">
    <article class="service" style="left:99px">
      <div class="service-icon is-filled">
        <svg width="32" height="32" viewBox="0 0 24 24"><path fill="#fff" d="M6.6 10.8a15.1 15.1 0 0 0 6.6 6.6l2.2-2.2c.3-.3.7-.4 1-.2 1.1.4 2.3.6 3.6.6.6 0 1 .4 1 1V20c0 .6-.4 1-1 1C10.6 21 3 13.4 3 4c0-.6.4-1 1-1h3.5c.6 0 1 .4 1 1 0 1.3.2 2.5.6 3.6.1.3 0 .7-.2 1z"/></svg>
      </div>
      <h2 class="service-title is-single">PBX</h2>
      <p class="service-text">Phasellus nisl est, condimentum vitae faucibus in, sollicitudin vel metus. Nunc sit amet consequat risus.</p>
    </article>
    <article class="service" style="left:368px">
      <div class="service-icon">
        <svg width="40" height="32" viewBox="0 0 40 32" fill="none" stroke="#0b2a5b" stroke-width="1.3" stroke-linecap="round" stroke-linejoin="round"><path d="M13 26H9a6 6 0 0 1 0-12 9 9 0 0 1 17-3 7 7 0 0 1 5 15h-4"/><path d="M20 29V15M15 20l5-5 5 5"/></svg>
      </div>
      <h2 class="service-title">IP/Cloud Based phone systems</h2>
      <p class="service-text">Phasellus nisl est, condimentum vitae faucibus in, sollicitudin vel metus. Nunc sit amet consequat risus.</p>
    </article>
    <article class="service" style="left:637px">
      <div class="service-icon">
        <svg width="40" height="26" viewBox="0 0 40 26" fill="none" stroke="#0b2a5b" stroke-width="1.3" stroke-linejoin="round"><rect x="2" y="3" width="26" height="20"/><path d="M28 10l10-6v18l-10-6"/><rect x="6" y="12" width="10" height="6"/><path d="M6 8h3"/></svg>
      </div>
      <h2 class="service-title">Video camera surveillance systems</h2>
      <p class="service-text">Phasellus nisl est, condimentum vitae faucibus in, sollicitudin vel metus. Nunc sit amet consequat risus.</p>
    </article>
    <article class="service" style="left:905px">
      <div class="service-icon">
        <svg width="24" height="40" viewBox="0 0 24 40" fill="none" stroke="#0b2a5b" stroke-width="1.3" stroke-linejoin="round"><path d="M15 2L4 22h8l-4 16 13-21h-8z"/></svg>
      </div>
      <h2 class="service-title">Low&nbsp; voltage cabling services</h2>
      <p class="service-text">Phasellus nisl est, condimentum vitae faucibus in, sollicitudin vel metus. Nunc sit amet consequat risus.</p>
    </article>
  </section>

  <section class="cta-band">
    <p class="cta-line">Aenean sed quam non sapien faucibus consequat vitae mollis nulla in pulvinar dictum.</p>
    <a class="cta-button" href="#">APPLY NOW</a>
  </section>

  <footer class="site-footer">
    <nav class="footer-nav">
      <a href="#">Home</a><span class="sep">|</span><a href="#">Phone systems</a><span class="sep">|</span><a href="#">Video Surveillance</a><span class="sep">|</span><a href="#">Low voltage cabling</a><span class="sep">|</span><a href="#">Carrier</a><span class="sep">|</span><a href="#">Contact us</a>
    </nav>
    <p class="copyright">Copyright &nbsp;©&nbsp; 2015 &nbsp;Tallow Ridge Communications. All rights reserved</p>
    <div class="social" aria-label="Social links">
      <span style="background:#3b5a9a"></span>
      <span style="background:#29b6e8"></span>
      <span style="background:#1f8fc0"></span>
    </div>
  </footer>
</body>
</html>
```